World leading Water filters German made

I am a local Plumbing business who is authorised water filter installer
I want to do a Flyer design double sided targeting niche market for Water Filters.
My company colours are black background with white writing.
( but happy to go into different colours to capture more people )
I want all my stuff, sleek and professional with the same fonts throughout.
Www.brightpipeandboiler.au
Is my website you can see how I do things there.
I want the local business awards finalist logo on the flyer too ( it’ll be in the photo)
This Flyer I want all about health and wellness making big points on water filtration benefits
Massive to included HYDROGEN WATER AND ALKALINE WATER ,
REMOVE FLUORIDE
I don’t know whether to have it with the pre-save branded information I sent over, but I don’t want the company other companies name everywhere
I want the main focus about my company Bright Pipe And Boiler Experts
I want the focus to be about a family owned and run Illawarra local business establish for over 20 years.
Please note I have included a Customer brochure the company has designed so you can see some key points on the second page about the products. I want this a lot more eye-catching and appealing please
Target Market(s)
Health and wellness people
Colors
Designer to choose colors to be used in the design.
Requirements
Must have
- Call Derek 0459 237 816, my website , social media buttons ,
Nice to have
- World leading , health and wellness ,
Should not have
- Any information to lead them away from calling myself , I’m the authorities dealer for clearspring supply but I want to no have as much anout them.

```html
<!DOCTYPE html>
<html lang="en">
<head>
<meta charset="utf-8">
<title>Bright Pipe And Boiler Experts – Double-Sided Flyer</title>
<link href="https://fonts.googleapis.com/css2?family=Michroma&family=Oswald:wght@500&family=Poppins:wght@400;500;600;700&display=swap" rel="stylesheet">
<style>
:root{
  --ink:#0d0d0f;
  --ink-2:#2b2b30;
  --white:#ffffff;
  --paper:#ffffff;
  --text-dark:#111216;
  --text-body:#3a3b40;
  --blue:#1ca7dc;
  --blue-deep:#0b5e84;
  --red:#e3202a;
  --red-deep:#a8121a;
  --gold:#c9a24a;
  --gold-light:#e4c677;
  --stage:#dfe5ec;
}
*{box-sizing:border-box;margin:0;padding:0}
html,body{width:852px;height:1200px;overflow:hidden;background:var(--stage)}
body{position:relative;font-family:"Poppins",sans-serif}

.flyer{position:absolute;top:341px;width:400px;height:518px;overflow:hidden;box-shadow:0 4px 14px rgba(0,0,0,.25)}
.flyer-front{left:18px;background:linear-gradient(180deg,var(--ink) 0%,#18181b 55%,var(--ink-2) 100%);color:var(--white)}
.flyer-back{left:434px;background:var(--paper);color:var(--text-dark)}

.brand{position:absolute;left:25px;top:24px;display:flex;align-items:center;gap:6px}
.brand-square{width:9px;height:9px;background:var(--white)}
.brand-name{font-family:"Michroma",sans-serif;font-size:8px;line-height:1.35;letter-spacing:.5px;color:var(--white)}

.headline{position:absolute;left:25px;font-family:"Michroma",sans-serif;font-size:16px;line-height:1.08;text-transform:uppercase;font-weight:400}
.headline .light{opacity:.85}

.seal{position:absolute;width:90px;height:90px}
.seal svg{position:absolute;inset:0}
.seal p{position:absolute;inset:0;display:flex;align-items:center;justify-content:center;text-align:center;font-size:5.5px;font-weight:600;line-height:1.25;padding:24px 20px;color:var(--white)}

/* front */
.front-headline{top:90px}
.product-photo{position:absolute;left:215px;top:45px;width:160px;height:155px;border-radius:4px;background:linear-gradient(160deg,#eceef1 0%,#a9adb4 55%,#2e3340 100%)}
.front-seal{left:163px;top:135px}
.athlete-photo{position:absolute;left:15px;top:165px;width:185px;height:335px;background:radial-gradient(ellipse at 50% 45%,#4a4d52 0%,#26272b 55%,rgba(20,20,22,0) 80%)}
.benefits-panel{position:absolute;left:118px;top:215px;width:262px;height:135px;background:var(--blue);border-radius:8px;padding:10px 14px}
.benefits-title{font-weight:600;font-size:10.5px;line-height:1.2;margin-bottom:10px}
.benefits-list{display:grid;grid-template-columns:1fr 1fr;row-gap:8px;column-gap:8px;list-style:none}
.benefits-list li{display:flex;align-items:center;gap:6px;font-size:6.5px;font-weight:500;line-height:1.2;text-transform:uppercase}
.hex{flex:0 0 16px;width:16px;height:16px}
.family{position:absolute;left:117px;top:356px}
.family-line{display:flex;align-items:center;gap:5px}
.family-owned{font-family:"Oswald",sans-serif;font-weight:500;font-size:20px;color:var(--red);line-height:1}
.family-note{font-size:7.5px;line-height:1.25}
.years{font-family:"Michroma",sans-serif;font-size:13px;color:var(--blue);letter-spacing:2px;margin-top:5px}
.award-badge{position:absolute;left:332px;top:332px;width:42px;height:68px}
.emergency{position:absolute;left:120px;top:410px;display:flex;align-items:center;gap:10px}
.emergency-mark{width:56px}
.emergency-mark .hours{font-family:"Oswald",sans-serif;font-size:20px;font-weight:500;color:var(--red);line-height:1}
.emergency-mark .label{font-size:6.5px;font-weight:700;line-height:1.2;text-transform:uppercase}
.emergency-note{width:195px;background:#2f3034;border-radius:5px;padding:5px 8px;font-size:6.5px;line-height:1.4}

.contact{position:absolute;display:flex;align-items:center;gap:8px}
.call{font-weight:700;font-size:11px;letter-spacing:.3px;white-space:nowrap}
.call .name{color:var(--blue)}
.phone-icon{width:9px;height:9px;vertical-align:-1px;margin:0 2px}
.social{display:flex;align-items:center;gap:4px;font-size:5px;line-height:1.2}
.social-dot{width:9px;height:9px;border-radius:50%;background:var(--blue)}
.website{position:absolute;font-size:11px;font-weight:600;letter-spacing:2.2px;white-space:nowrap}
.website .domain{color:var(--blue)}
.front-contact{left:128px;top:466px}
.front-website{left:128px;top:482px}

/* back */
.back-top{position:absolute;left:0;top:0;width:400px;height:230px;background:var(--ink)}
.woman-photo{position:absolute;left:215px;top:0;width:185px;height:215px;background:linear-gradient(200deg,#7a5a48 0%,#5a6a74 35%,#2a2c30 100%)}
.water-splash{position:absolute;left:0;top:140px;width:400px;height:120px}
.back .brand{top:24px}
.back-headline{top:80px;color:var(--white)}
.back-headline .accent{color:var(--red)}
.back-headline .strong{font-weight:400;text-shadow:0 0 .6px #fff}
.back-seal{left:295px;top:150px}
.feature{position:absolute;width:175px}
.feature h3{font-size:8.5px;font-weight:700;line-height:1.1;text-transform:uppercase;color:var(--text-dark);margin-bottom:4px}
.feature p{font-size:5px;line-height:1.4;color:var(--text-body)}
.f-hard{left:25px;top:258px}
.f-chem{left:215px;top:258px;width:162px}
.f-uv{left:25px;top:338px}
.f-arch{left:215px;top:338px;width:162px}
.health{position:absolute;left:25px;top:410px;width:345px;height:62px;background:var(--blue);border-radius:6px}
.health-tab{position:absolute;left:0;top:0;width:165px;height:18px;background:var(--red);clip-path:polygon(0 0,100% 0,92% 100%,0 100%);border-radius:6px 0 0 0;color:var(--white);font-size:9px;font-weight:700;letter-spacing:1.5px;padding:3px 0 0 14px;line-height:1.3}
.health-cols{position:absolute;left:14px;top:24px;right:10px;display:grid;grid-template-columns:1fr 1fr 1fr;column-gap:8px;list-style:none}
.health-cols ul{list-style:none}
.health-cols li{font-size:4.6px;line-height:1.5;color:var(--white);display:flex;align-items:center;gap:3px}
.health-cols li::before{content:"";width:3px;height:3px;border-radius:50%;background:var(--white);flex:0 0 3px}
.back-contact{left:25px;top:478px}
.back-contact .call .number{color:var(--text-dark)}
.back-website{left:25px;top:492px;font-size:10px;letter-spacing:1.9px;color:var(--text-dark)}
.back-social{position:absolute;left:262px;top:484px;color:var(--text-dark)}
</style>
</head>
<body>

<main class="flyer flyer-front">
  <div class="brand"><span class="brand-square"></span><span class="brand-name">BRIGHT PIPE<br>&amp; BOILER EXPERTS</span></div>
  <h1 class="headline front-headline"><span class="light">Bright</span><br>Pipe And<br>Boiler<br>Experts</h1>

  <div class="product-photo" role="img" aria-label="Stainless steel whole-house water filter unit with filter cartridges"></div>
  <div class="athlete-photo" role="img" aria-label="Athletic man in a neon vest drinking water with a towel over his shoulder"></div>

  <div class="seal front-seal">
    <svg viewBox="0 0 150 150" width="90" height="90" aria-hidden="true">
      <polygon fill="var(--red-deep)" points="75,2 87,14 103,8 109,24 126,24 126,41 142,47 136,63 148,75 136,87 142,103 126,109 126,126 109,126 103,142 87,136 75,148 63,136 47,142 41,126 24,126 24,109 8,103 14,87 2,75 14,63 8,47 24,41 24,24 41,24 47,8 63,14"/>
      <circle cx="75" cy="75" r="52" fill="var(--red)"/>
      <circle cx="75" cy="75" r="46" fill="none" stroke="#fff" stroke-width="1.2" stroke-dasharray="2 3"/>
    </svg>
    <p>We service Illawarra, Wollongong, Shellharbour &amp; Shoalhaven areas.</p>
  </div>

  <section class="benefits-panel">
    <h2 class="benefits-title">Your Complete Home Water<br>Filtration German Solution:</h2>
    <ul class="benefits-list">
      <li><svg class="hex" viewBox="0 0 30 30"><polygon points="15,1 28,8 28,22 15,29 2,22 2,8" fill="var(--blue-deep)"/><circle cx="15" cy="15" r="5" fill="#fff"/></svg>Hard water<br>anti-scale protection</li>
      <li><svg class="hex" viewBox="0 0 30 30"><polygon points="15,1 28,8 28,22 15,29 2,22 2,8" fill="var(--blue-deep)"/><path d="M15 8 C19 14 20 16 20 18 A5 5 0 0 1 10 18 C10 16 11 14 15 8Z" fill="#fff"/></svg>Hydrogen water and<br>alkaline water</li>
      <li><svg class="hex" viewBox="0 0 30 30"><polygon points="15,1 28,8 28,22 15,29 2,22 2,8" fill="var(--blue-deep)"/><path d="M10 15 L14 19 L21 11" stroke="#fff" stroke-width="2.5" fill="none"/></svg>Chemical removal</li>
      <li><svg class="hex" viewBox="0 0 30 30"><polygon points="15,1 28,8 28,22 15,29 2,22 2,8" fill="var(--blue-deep)"/><path d="M10 10 L20 20 M20 10 L10 20" stroke="#fff" stroke-width="2.5"/></svg>Remove fluoride</li>
      <li><svg class="hex" viewBox="0 0 30 30"><polygon points="15,1 28,8 28,22 15,29 2,22 2,8" fill="var(--blue-deep)"/><circle cx="15" cy="15" r="4" fill="#fff"/><path d="M15 7v3M15 20v3M7 15h3M20 15h3" stroke="#fff" stroke-width="2"/></svg>Ultraviolet<br>protection</li>
      <li><svg class="hex" viewBox="0 0 30 30"><polygon points="15,1 28,8 28,22 15,29 2,22 2,8" fill="var(--blue-deep)"/><rect x="11" y="8" width="8" height="14" rx="2" fill="#fff"/></svg>Free filters<br>for life</li>
    </ul>
  </section>

  <section class="family">
    <div class="family-line">
      <span class="family-owned">FAMILY OWNED</span>
      <span class="family-note">and run Illawarra local<br>business establish for</span>
    </div>
    <div class="years">OVER 20 YEARS.</div>
  </section>

  <svg class="award-badge" viewBox="0 0 42 68" role="img" aria-label="Local business awards finalist badge">
    <circle cx="21" cy="21" r="20" fill="var(--gold)"/>
    <circle cx="21" cy="21" r="15" fill="var(--gold-light)"/>
    <rect x="6" y="42" width="30" height="25" fill="var(--red)"/>
  </svg>

  <section class="emergency">
    <div class="emergency-mark">
      <div class="hours">24/7</div>
      <div class="label">Emergency<br>plumbing</div>
    </div>
    <p class="emergency-note">Just give us a call, and we'll jump into action right away. Our expert plumbers will sort out all your plumbing without any delay.</p>
  </section>

  <div class="contact front-contact">
    <span class="call"><span class="name">CALL DEREK</span><svg class="phone-icon" viewBox="0 0 24 24"><circle cx="12" cy="12" r="12" fill="var(--red)"/><path d="M8 6c1 0 2 3 1.5 3.5L8.5 10.5c.8 2 2.5 3.7 5 5l1-1c.5-.5 3.5.5 3.5 1.5v1c0 1-1 1.5-2 1.5C10 18.5 5.5 14 5.5 8 5.5 7 6 6 7 6Z" fill="#fff"/></svg>0459 237 816</span>
    <span class="social"><span class="social-dot"></span>@Bright Pipe and<br>Boiler Experts</span>
  </div>
  <div class="website front-website">www.<span class="domain">brightpipeandboiler</span>.au</div>
</main>

<main class="flyer flyer-back back">
  <div class="back-top"></div>
  <div class="woman-photo" role="img" aria-label="Woman in sportswear drinking from a water bottle beside a stainless filter unit"></div>
  <svg class="water-splash" viewBox="0 0 400 120" preserveAspectRatio="none" role="img" aria-label="Blue water splash wave">
    <defs><linearGradient id="wave" x1="0" y1="0" x2="0" y2="1"><stop offset="0" stop-color="#6fd3f5"/><stop offset="1" stop-color="#0f7fb0"/></linearGradient></defs>
    <path d="M0 60 C60 30 120 40 170 55 C220 70 260 10 320 30 C360 42 385 55 400 50 L400 95 C340 110 300 90 250 98 C180 110 120 90 60 105 C30 112 10 112 0 110 Z" fill="url(#wave)"/>
  </svg>

  <div class="brand"><span class="brand-square"></span><span class="brand-name">BRIGHT PIPE<br>&amp; BOILER EXPERTS</span></div>
  <h1 class="headline back-headline">Your<br>Complete<br><span class="accent">Home Water</span><br><span class="accent">Filtration</span><br><span class="strong">Solution</span></h1>

  <div class="seal back-seal">
    <svg viewBox="0 0 150 150" width="90" height="90" aria-hidden="true">
      <polygon fill="var(--red-deep)" points="75,2 87,14 103,8 109,24 126,24 126,41 142,47 136,63 148,75 136,87 142,103 126,109 126,126 109,126 103,142 87,136 75,148 63,136 47,142 41,126 24,126 24,109 8,103 14,87 2,75 14,63 8,47 24,41 24,24 41,24 47,8 63,14"/>
      <circle cx="75" cy="75" r="52" fill="var(--red)"/>
      <circle cx="75" cy="75" r="46" fill="none" stroke="#fff" stroke-width="1.2" stroke-dasharray="2 3"/>
    </svg>
    <p>We service Illawarra, Wollongong, Shellharbour &amp; Shoalhaven areas.</p>
  </div>

  <section class="feature f-hard">
    <h3>Hardwater<br>Anti-Scale Protection</h3>
    <p>Combat your hard water problems naturally, not chemically. Our salt-free technology stops scale building up in pipes, taps and appliances, protecting your hot water system and keeping skin and hair soft. Ask about our healthier option for you and the environment.</p>
  </section>
  <section class="feature f-chem">
    <h3>Chemical Removal</h3>
    <p>Removing chemicals from your water using world leading German technology. Chlorine, pesticides and heavy metals are filtered out at every tap, so the whole family enjoys cleaner, fresher water for drinking, cooking and showering every day of the year.</p>
  </section>
  <section class="feature f-uv">
    <h3>Ultraviolet Protection</h3>
    <p>Protecting your family from bacteria and waterborne viruses is paramount. Our chemical-free ultraviolet stage kills 99.9% of bacteria, leaving your water safe for drinking. It is the perfect solution for rainwater tanks and homes on the coast.</p>
  </section>
  <section class="feature f-arch">
    <h3>Architectural Range</h3>
    <p>Unlimited possibilities with our architectural range, designed to elevate your home with high-end finishes. Built from 304 stainless steel, each unit sets the benchmark with a choice of 30 distinct colour options and finishes.</p>
  </section>

  <section class="health">
    <div class="health-tab">HEALTH BENEFITS</div>
    <div class="health-cols">
      <ul><li>Reduce the risk of cancer</li><li>Relief for eczema sufferers</li><li>Anti-Aging benefits</li><li>Improved skin conditions</li></ul>
      <ul><li>Reduce the risk of birth defects</li><li>Relief for asthma sufferers</li><li>Enjoy chemical free showering</li><li>Improved hair conditions</li></ul>
      <ul><li>Healthier drinking water</li><li>Alkaline pH + water</li><li>Reduced daily chemical exposure</li></ul>
    </div>
  </section>

  <div class="contact back-contact">
    <span class="call"><span class="name">CALL DEREK</span><svg class="phone-icon" viewBox="0 0 24 24"><circle cx="12" cy="12" r="12" fill="var(--red)"/><path d="M8 6c1 0 2 3 1.5 3.5L8.5 10.5c.8 2 2.5 3.7 5 5l1-1c.5-.5 3.5.5 3.5 1.5v1c0 1-1 1.5-2 1.5C10 18.5 5.5 14 5.5 8 5.5 7 6 6 7 6Z" fill="#fff"/></svg><span class="number">0459 237 816</span></span>
  </div>
  <div class="website back-website">www.<span class="domain">brightpipeandboiler</span>.au</div>
  <span class="social back-social"><span class="social-dot"></span>@Bright Pipe and<br>Boiler Experts</span>
</main>

</body>
</html>
```